Business card for Bio pharmaceutical company

Hello,
We are a bio pharmaceutical contract manufacturing company in Brisbane, Australia. Can you please create a new business card design. Please go to our website for colours http://www.corvalinbio.com.au.
On the back can you include the cartoon mascot Tobi Tumlo and the tagline
"A Global Biopharmaceutical Contract Development Manufacturing Company"
Target Market(s)
Biotechnology
Industry/Entity Type
Pharmaceutical
Contact Information for Business Card
Maren Holtby
Business Development Manager
maren.holtby@corvalinbio.com.au
1947 Kestrel Road Marlow Queesnland 4183 Australia
T: +61 7 3951 4820
M +61 415 206 718
F +61 7 3842 6093
www.corvalinbio.com.au

```html
<!DOCTYPE html>
<html lang="en">
<head>
<meta charset="utf-8">
<title>CorvalinBio Business Card</title>
<link href="https://fonts.googleapis.com/css2?family=Lato:wght@400;700&display=swap" rel="stylesheet">
<style>
  :root {
    --backdrop: #dbe5f5;
    --card: #ffffff;
    --brand-blue: #0b95c9;
    --headline-blue: #2b93c6;
    --navy: #1d3c68;
    --lime: #a9c53c;
    --ink: #1a1a1a;
    --white: #ffffff;
  }
  * { margin: 0; padding: 0; box-sizing: border-box; }
  html, body { width: 1200px; height: 965px; overflow: hidden; }
  body {
    background: radial-gradient(ellipse at center, #e8eefa 0%, var(--backdrop) 75%);
    font-family: 'Lato', sans-serif;
    position: relative;
  }
  .card {
    position: absolute;
    left: 285px;
    width: 630px;
    height: 360px;
    background: var(--card);
    box-shadow: 0 2px 8px rgba(30, 50, 90, 0.25);
    overflow: hidden;
  }
  .card--front { top: 80px; }
  .card--back { top: 525px; }

  /* Front */
  .tagline {
    position: absolute;
    left: 17px;
    top: 101px;
    font-weight: 700;
    font-size: 27.5px;
    line-height: 34px;
    color: var(--headline-blue);
    text-shadow: 1px 2px 2px rgba(0, 0, 0, 0.18);
    letter-spacing: -0.2px;
  }
  .site-link {
    position: absolute;
    left: 22px;
    top: 320px;
    font-weight: 700;
    font-size: 20px;
    color: var(--headline-blue);
    text-decoration: none;
  }
  .site-link .domain { color: var(--lime); }
  .mascot {
    position: absolute;
    left: 405px;
    top: 18px;
    width: 200px;
    height: 245px;
    border-radius: 50px;
    background: radial-gradient(ellipse at center, #5cc0e8 0%, #2a9fd6 55%, rgba(42,159,214,0.15) 100%);
  }
  .front-brand {
    position: absolute;
    left: 424px;
    top: 268px;
    display: flex;
    align-items: center;
    gap: 8px;
    font-weight: 700;
    font-size: 25px;
    color: var(--navy);
  }
  .front-brand .mark {
    width: 16px; height: 16px;
    background: var(--navy);
  }
  .slogan-lettering {
    position: absolute;
    left: 400px;
    top: 302px;
    width: 218px;
    height: 36px;
    border-radius: 6px;
    background: linear-gradient(90deg, #1f3f6e, #2a5388);
    opacity: 0.85;
  }

  /* Back */
  .name-row {
    position: absolute;
    left: 16px;
    top: 24px;
    display: flex;
    align-items: center;
    gap: 12px;
  }
  .name {
    font-weight: 700;
    font-size: 24px;
    color: var(--ink);
  }
  .name-divider {
    width: 2px; height: 18px;
    background: var(--navy);
  }
  .role { font-size: 15.5px; color: var(--ink); }
  .rule {
    position: absolute;
    left: 0; width: 100%;
    height: 3px;
    background: var(--navy);
  }
  .rule--top { top: 85px; }
  .rule--bottom { top: 307px; }
  .band {
    position: absolute;
    left: 0; top: 90px;
    width: 100%; height: 216px;
    background: var(--brand-blue);
  }
  .back-brand {
    position: absolute;
    left: 16px;
    top: 78px;
    display: flex;
    align-items: center;
    gap: 8px;
    font-weight: 700;
    font-size: 28px;
    color: var(--white);
  }
  .back-brand .mark {
    width: 18px; height: 18px;
    background: var(--white);
  }
  .band-divider {
    position: absolute;
    left: 263px; top: 30px;
    width: 1px; height: 158px;
    background: rgba(255,255,255,0.7);
  }
  .contact {
    position: absolute;
    left: 272px;
    top: 24px;
    color: var(--white);
    font-size: 18.5px;
    line-height: 23px;
  }
  .address { margin-bottom: 15px; }
  .contact-list { list-style: none; }
  .contact-list li {
    display: flex;
    align-items: center;
    gap: 9px;
    height: 23px;
  }
  .contact-list svg { width: 19px; height: 19px; flex: none; }
</style>
</head>
<body>

<section class="card card--front">
  <h1 class="tagline">A Global<br>Biopharmaceutical<br>Contract Development<br>Manufacturing Company</h1>
  <a class="site-link" href="http://www.corvalinbio.com.au">www.<span class="domain">corvalinbio</span>.com.au</a>
  <div class="mascot" role="img" aria-label="Company mascot illustration"></div>
  <div class="front-brand"><span>CorvalinBio</span><span class="mark"></span></div>
  <div class="slogan-lettering" role="img" aria-label="Hand-lettered slogan"></div>
</section>

<section class="card card--back">
  <div class="name-row">
    <span class="name">Maren Holtby</span>
    <span class="name-divider"></span>
    <span class="role">Business Development Manager</span>
  </div>
  <div class="rule rule--top"></div>
  <div class="band">
    <div class="back-brand"><span>CorvalinBio</span><span class="mark"></span></div>
    <div class="band-divider"></div>
    <div class="contact">
      <p class="address">1947 Kestrel Road<br>Marlow Queesnland 4183 Australia</p>
      <ul class="contact-list">
        <li>
          <svg viewBox="0 0 20 20" fill="#fff"><path d="M3 7c0-2 3-3 7-3s7 1 7 3v1h-4V6.5c-1-.4-5-.4-6 0V8H3z"/><path d="M6 9h8l2 7H4z"/><circle cx="10" cy="12.5" r="1.6" fill="#0b95c9"/></svg>
          <span>+61 7 3951 4820</span>
        </li>
        <li>
          <svg viewBox="0 0 20 20" fill="none" stroke="#fff" stroke-width="1.6"><rect x="6" y="2.5" width="8" height="15" rx="1.5"/><line x1="9" y1="15" x2="11" y2="15"/></svg>
          <span>+61 415 206 718</span>
        </li>
        <li>
          <svg viewBox="0 0 20 20" fill="#fff"><rect x="6" y="3" width="8" height="4"/><rect x="3" y="8" width="14" height="6" rx="1"/><rect x="6" y="12" width="8" height="5" stroke="#0b95c9" stroke-width="1"/></svg>
          <span>+61 7 3842 6093</span>
        </li>
        <li>
          <svg viewBox="0 0 20 20" fill="none" stroke="#fff" stroke-width="1.6"><rect x="2.5" y="5" width="15" height="10"/><polyline points="2.5,5 10,11 17.5,5"/></svg>
          <span>maren.holtby@corvalinbio.com.au</span>
        </li>
        <li>
          <svg viewBox="0 0 20 20" fill="none" stroke="#fff" stroke-width="1.5"><circle cx="10" cy="10" r="7.5"/><ellipse cx="10" cy="10" rx="3.2" ry="7.5"/><line x1="2.5" y1="10" x2="17.5" y2="10"/></svg>
          <span>www.corvalinbio.com.au</span>
        </li>
      </ul>
    </div>
  </div>
  <div class="rule rule--bottom"></div>
</section>

</body>
</html>
```